Business Card Design

I need a logo and a business card design that can be used for my business stationary, Facebook page and in the future a website. I don't know if I need a large design for brochures and stationery and a small portion of that as the logo or business card design. I probably need some advice about that. My new company is called Willowbank Family Circle. I don't have all of my business contact details available yet, but I want to get the design ready, so that when all this information is available I can get the printing done quickly.I'm a social worker and my business will be providing parenting groups and counselling sessions for parents.I would like the logo and business card to be very feminine and pretty. I want a silhouette image of a Mother and Baby and decorative swirls of flowers/vines/leaves and butterflies.I have found some designs elsewhere that are along the lines of what I am looking for. These images are attached below, but the quality of these attachments is very poor as I photographed them with my phone.My preferred colours would be to use black and white, purple and/or pink, aqua and or blue/green.There are four logo/business card options attached. Logo option 1 - I really like the flower and vine design. Logo option 2 - again I like the flowers and leaf design and the use of colour and the silhouette image of the Mum and Baby; Logo option 3 - I like the butterflies and decorative swirls in this option and Logo option 4 - I think this design is the best for a logo. I love the mother and baby image. I don't like the tree branch and the birds but I like the way the hair has been incorporated into the branch. I prefer the design of the flowers/vine/leaves in the other options.

Industry/Entity Type

Business

Contact Information for Business Card

Company Name:Embrace Attachment ParentingMobile:0417 751 394Email:Currently sourcing - TBAContact Name:Janelle ApplegarthQualifications:Currently sourcing details - TBA

Font styles to use
Script

Colors
33a6d7
85cae6
886aae
6c459b
e667a6
eea4c8

Requirements
Must have
• My project must have an image of a mother and child, slightly encircled by the mother's hair perhaps in a heart shape, and the mother's hair becoming a beautiful filigree design of vine/leaves/flowers and with some butterfly somewhere.
• Can all of the Words be in the same font Attachment Parenting can be slightly smaller.
Nice to have
• I would like to also have a similar vine/leaves/flowers and maybe a butterfly on the opposite side of the card. Maybe the Mother/child image on the top left of the card and the other pattern on the bottom right.
• If possible the use of aqua, purple and pink.

```html
<!DOCTYPE html>
<html lang="en">
<head>
<meta charset="utf-8">
<title>Willowbank Family Circle – Business Card</title>
<link rel="stylesheet" href="https://fonts.googleapis.com/css2?family=Poiret+One&family=Questrial&display=swap">
<style>
  :root {
    --page-bg: #ece7e1;
    --card-bg: #ffffff;
    --green-dark: #4f8a3b;
    --green-light: #8cc63f;
    --green-pale: #c4e29a;
  }
  html, body {
    margin: 0;
    width: 1200px;
    height: 902px;
    overflow: hidden;
    background: var(--page-bg);
  }
  .business-card {
    position: absolute;
    left: 40px;
    top: 132px;
    width: 1120px;
    height: 637px;
    background: var(--card-bg);
    box-shadow: 0 6px 24px rgba(0,0,0,0.12);
    overflow: hidden;
  }
  .brand {
    position: absolute;
    left: 40px;
    top: 110px;
    width: 520px;
    text-align: center;
  }
  .brand-dot {
    display: block;
    width: 170px;
    height: 170px;
    margin: 0 auto 34px;
    border-radius: 50%;
    background: var(--green-pale);
  }
  .brand-name {
    margin: 0;
    font-family: "Poiret One", sans-serif;
    font-weight: 400;
    font-size: 56px;
    line-height: 1.1;
    color: var(--green-dark);
  }
  .contact {
    position: absolute;
    left: 582px;
    top: 70px;
  }
  .contact-name {
    margin: 0;
    font-family: "Poiret One", sans-serif;
    font-weight: 400;
    font-size: 50px;
    line-height: 1;
    color: var(--green-dark);
  }
  .contact-role {
    margin: 6px 0 0;
    font-family: "Questrial", sans-serif;
    font-size: 28px;
    color: var(--green-light);
  }
  .contact-lines {
    list-style: none;
    margin: 54px 0 0;
    padding: 0;
    font-family: "Questrial", sans-serif;
    font-size: 31px;
    color: var(--green-dark);
  }
  .contact-lines li {
    display: flex;
    align-items: center;
    gap: 12px;
    height: 38px;
  }
  .contact-icon {
    width: 27px;
    height: 27px;
    flex: none;
  }
  .corner-ornament {
    position: absolute;
    right: 0;
    bottom: 0;
    width: 495px;
    height: 312px;
  }
</style>
</head>
<body>
  <main class="business-card">
    <section class="brand">
      <span class="brand-dot" aria-hidden="true"></span>
      <h1 class="brand-name">Willowbank<br>Family Circle</h1>
    </section>

    <section class="contact">
      <h2 class="contact-name">Rosalind Thackeray</h2>
      <p class="contact-role">Currently sourcing details - TBA</p>
      <ul class="contact-lines">
        <li>
          <svg class="contact-icon" viewBox="0 0 27 27" aria-hidden="true">
            <rect width="27" height="27" fill="#8cc63f"/>
            <rect x="8" y="4" width="11" height="19" rx="2" fill="none" stroke="#fff" stroke-width="2"/>
            <rect x="10" y="7" width="7" height="6" fill="#fff"/>
          </svg>
          <span>0438 260 517</span>
        </li>
        <li>
          <svg class="contact-icon" viewBox="0 0 27 27" aria-hidden="true">
            <rect width="27" height="27" fill="#8cc63f"/>
            <rect x="4" y="7" width="19" height="13" fill="none" stroke="#fff" stroke-width="2"/>
            <path d="M4 7 L13.5 15 L23 7" fill="none" stroke="#fff" stroke-width="2"/>
          </svg>
          <span>Currently sourcing - TBA</span>
        </li>
      </ul>
    </section>

    <svg class="corner-ornament" viewBox="0 0 495 312" role="img"
         aria-label="Decorative swirl of green vines, leaves and flowers in the lower right corner">
      <defs>
        <linearGradient id="vine-tone" x1="0" y1="1" x2="1" y2="0">
          <stop offset="0" stop-color="#8cc63f" stop-opacity="0.55"/>
          <stop offset="1" stop-color="#4f8a3b" stop-opacity="0.7"/>
        </linearGradient>
      </defs>
      <path d="M0 312 C60 280 110 250 170 200 C230 150 300 150 360 110 C400 80 420 40 450 0 L495 0 L495 312 Z"
            fill="url(#vine-tone)"/>
    </svg>
  </main>
</body>
</html>
```